Harborline Renewal Business Card Design

Professional and clean design. The design colors should flow with the logo. Two-sided card with the website on the back which is:

www.HarborlineRenewal.example.

"Specializing in Water Damage Restoration"

On the front I need the name, email, phone, and logo.

Name: Darnell Quisby
Email: Darnell@HarborlineRenewal.example
Phone: 555-318-2046 for now

I only have the Preview and Thumbnail right now but should have the source files uploaded within a day or two.

Target Market(s)

Flood victims, home owners with water damage from busted pipes etc...

Industry/Entity Type

Business

Contact Information for Business Card

Name: Darnell Quisby

Font styles to use
Serif
Sans Serif

Requirements
Must have
• Business Card Details Info

```html
<!DOCTYPE html>
<html lang="en">
<head>
<meta charset="utf-8">
<title>Harborline Renewal Business Card</title>
<link rel="stylesheet" href="https://fonts.googleapis.com/css2?family=Cinzel:wght@400&family=Open+Sans:wght@400;600&display=swap">
<style>
  :root {
    --stage: #000000;
    --card-white: #ffffff;
    --brand-blue: #2a9fd6;
    --sky-top: #56c4f1;
    --sky-bottom: #33a2dc;
    --ink: #1e1e1e;
    --on-blue: #ffffff;
  }
  * { margin: 0; padding: 0; box-sizing: border-box; }
  html, body { width: 1200px; height: 900px; overflow: hidden; background: var(--stage); }
  .stage { position: relative; width: 1200px; height: 900px; }

  .card { position: absolute; top: 200px; width: 310px; height: 502px; overflow: hidden; }

  .card-front {
    left: 265px;
    background: var(--card-white);
    border-radius: 58px 0 58px 0;
  }
  .card-back {
    left: 641px;
    width: 309px;
    background: linear-gradient(180deg, var(--sky-top) 0%, var(--sky-bottom) 100%);
    border-radius: 0 58px 0 58px;
  }

  .brand-dot {
    position: absolute; left: 117px; top: 37px;
    width: 76px; height: 76px; border-radius: 50%;
    background: var(--brand-blue);
  }
  .wordmark {
    position: absolute; left: 0; right: 0;
    font-family: "Cinzel", "Times New Roman", serif;
    font-weight: 400; text-align: center;
    line-height: 1.15; letter-spacing: 1px;
  }
  .card-front .wordmark { top: 126px; font-size: 30px; color: var(--brand-blue); }
  .card-back .wordmark { top: 310px; font-size: 30px; color: var(--on-blue); }

  .holder-name {
    position: absolute; left: 23px; top: 388px;
    font-family: "Open Sans", Arial, sans-serif;
    font-weight: 600; font-size: 18px; color: var(--brand-blue);
  }
  .contact-list { position: absolute; left: 23px; top: 430px; list-style: none; }
  .contact-item {
    display: flex; align-items: center; gap: 5px;
    font-family: "Open Sans", Arial, sans-serif;
    font-size: 13px; color: var(--ink); height: 21px;
  }
  .contact-icon { width: 10px; height: 10px; fill: var(--brand-blue); flex: none; }

  .tagline, .website {
    position: absolute; left: 0; right: 0; text-align: center;
    font-family: "Open Sans", Arial, sans-serif; font-weight: 600; color: var(--on-blue);
  }
  .tagline { top: 398px; font-size: 14px; }
  .website { top: 443px; font-size: 13px; }
</style>
</head>
<body>
<main class="stage">
  <section class="card card-front" aria-label="Card front">
    <div class="brand-dot"></div>
    <h1 class="wordmark">Harborline<br>Renewal</h1>
    <p class="holder-name">Darnell Quisby</p>
    <ul class="contact-list">
      <li class="contact-item">
        <svg class="contact-icon" viewBox="0 0 24 24" aria-hidden="true"><path d="M6.6 10.8a15.1 15.1 0 0 0 6.6 6.6l2.2-2.2a1 1 0 0 1 1-.25 11.4 11.4 0 0 0 3.6.57 1 1 0 0 1 1 1V20a1 1 0 0 1-1 1A17 17 0 0 1 3 4a1 1 0 0 1 1-1h3.5a1 1 0 0 1 1 1c0 1.25.2 2.45.57 3.57a1 1 0 0 1-.25 1z"/></svg>
        555-318-2046
      </li>
      <li class="contact-item">
        <svg class="contact-icon" viewBox="0 0 24 24" aria-hidden="true"><path d="M2 5h20v14H2z M2 5l10 8 10-8" /></svg>
        Darnell@HarborlineRenewal.example
      </li>
    </ul>
  </section>

  <section class="card card-back" aria-label="Card back">
    <h2 class="wordmark">Harborline Renewal</h2>
    <p class="tagline">Specializing in Water Damage Restoration</p>
    <p class="website">www.HarborlineRenewal.example</p>
  </section>
</main>
</body>
</html>
```